Tally Roster survey and prize

We need an A4 poster design for a survey and competition I wish to hold. The survey will be on Poll Heron. My website www.TallyRoster.com.au will redirect the users to the survey page. I will be selecting a survey entrant at random to win a prize. The prize is $200 cash. The survey will be open for two months as the mail out of this poster will go throughout Victoria, Australia. The competition end date is yet to be decided - depends on when I can get this poster completed and the mail out done.

The mail out is targeting the Aged Care industry workers and decision makers. It hopefully will be placed on a notice board in the facilities and need to attract attention for people to visit my site and then take the survey.

The survey is for not for residents but for the workers in the facility.

Reason: Just got some feedback on required content of the poster. Text for the poster required: "The survey is for determining a market for rostering and payroll software, your assitance in taking this survey would be greatly appreciated." Martin Holloway

Target Market(s)

Workers in Aged Care industry and decision makers.

Industry/Entity Type

Industry

Requirements
Must have
• 1. Must reference the website www.TallyRoster.com.au.
2. Must mention that there is a prize of $200.
3. Must mention that entry to the competition is dependant on taking the survey.
4. Must mention the close date (date yet to be decided).
5. Must mention winning contestant will be contacted by phone.

```html
<!DOCTYPE html>
<html lang="en">
<head>
<meta charset="utf-8">
<title>Tally Roster – How's Work Going? Survey Poster</title>
<link rel="stylesheet" href="https://fonts.googleapis.com/css2?family=Archivo+Black&family=Arimo:wght@700&family=Open+Sans:ital,wght@0,300;1,300&display=swap">
<style>
  :root {
    --sky: #00acec;
    --canopy: #2a9bd2;
    --canopy-deep: #1b8cc4;
    --ground: #1283ba;
    --white: #ffffff;
    --soft-white: #eef6fb;
    --prize-yellow: #fff212;
    --shadow-blue: #0c7fc0;
    --ink: #2f4a5c;
    --mascot: #2f7fd0;
  }
  * { margin: 0; padding: 0; box-sizing: border-box; }
  html, body { width: 912px; height: 1200px; overflow: hidden; }
  body { background: var(--sky); }

  .poster {
    position: relative;
    width: 912px;
    height: 1200px;
    background: var(--sky);
    overflow: hidden;
  }

  .headline {
    position: absolute;
    left: 0; top: 0;
    width: 912px; height: 400px;
  }
  .headline text {
    font-family: "Archivo Black", "Arial Black", sans-serif;
    fill: var(--white);
  }

  .mascot {
    position: absolute;
    left: 589px; top: 71px;
    width: 63px; height: 57px;
    border-radius: 45% 45% 40% 40%;
    background: var(--mascot);
  }

  .scene {
    position: absolute;
    left: 93px; top: 468px;
    width: 747px; height: 394px;
    background:
      radial-gradient(ellipse 60% 45% at 20% 30%, var(--canopy) 0%, rgba(42,155,210,0) 100%),
      radial-gradient(ellipse 45% 40% at 88% 35%, var(--canopy) 0%, rgba(42,155,210,0) 100%),
      linear-gradient(180deg, rgba(42,155,210,0.35) 0%, var(--canopy-deep) 60%, var(--ground) 100%);
    border-radius: 180px 160px 0 0 / 120px 110px 0 0;
  }

  .call-to-action,
  .prize {
    position: absolute;
    left: 0;
    width: 912px;
  }
  .call-to-action { top: 860px; height: 60px; }
  .call-to-action text {
    font-family: "Arimo", Arial, sans-serif;
    font-weight: 700;
    font-size: 37px;
    fill: var(--soft-white);
  }

  .prize { top: 900px; height: 160px; }
  .prize text {
    font-family: "Archivo Black", "Arial Black", sans-serif;
    font-size: 154px;
  }
  .prize .shadow { fill: var(--shadow-blue); }
  .prize .win { fill: var(--prize-yellow); }
  .prize .amount { fill: var(--white); }

  .details {
    position: absolute;
    left: 0; top: 1064px;
    width: 912px;
    text-align: center;
    font-family: "Open Sans", Arial, sans-serif;
    font-weight: 300;
    font-size: 17.5px;
    line-height: 23px;
    color: var(--ink);
    padding-left: 20px;
  }
  .details .site { font-style: italic; }
</style>
</head>
<body>
<main class="poster">

  <svg class="headline" viewBox="0 0 912 400" aria-label="How's work going?">
    <text x="109" y="203" font-size="124" textLength="696" lengthAdjust="spacingAndGlyphs">HOW’S WORK</text>
    <text x="92" y="380" font-size="206" textLength="731" lengthAdjust="spacingAndGlyphs">GOING?</text>
  </svg>

  <div class="mascot" role="img" aria-label="Small blue bird mascot perched on the headline"></div>

  <div class="scene" role="img" aria-label="Illustration of a smiling aged care worker in green scrubs and an elderly resident with a walking frame in a park with blue trees"></div>

  <svg class="call-to-action" viewBox="0 0 912 60" aria-label="Participate in the survey and be in to">
    <text x="141" y="43" textLength="616" lengthAdjust="spacingAndGlyphs">Participate in the survey and be in to</text>
  </svg>

  <svg class="prize" viewBox="0 0 912 160" aria-label="Win $200">
    <text class="shadow" x="100" y="138" textLength="297" lengthAdjust="spacingAndGlyphs">WIN</text>
    <text class="shadow" x="431" y="138" textLength="371" lengthAdjust="spacingAndGlyphs">$200</text>
    <text class="win" x="109" y="143" textLength="297" lengthAdjust="spacingAndGlyphs">WIN</text>
    <text class="amount" x="440" y="143" textLength="371" lengthAdjust="spacingAndGlyphs">$200</text>
  </svg>

  <p class="details">
    Please take the time to fill in this survey at <span class="site">www.TallyRoster.com.au</span> to enter the draw<br>
    Hurry! survey closes on &nbsp;00/00/2012 and the winner will be contacted by phone.
  </p>

</main>
</body>
</html>
```